Web Design for Webdesign company 3 page PSD

Project
---------
We need a PSD Web Design to be used in a WordPress installation.
What we would like to create is a professional looking website for a web design agency. We also need you to look for suitable stock images to be placed on these pages.
We need the design for:
Homepage
Landing page
Contact page
attached in the pages file you will find a file with more in depth details how these files should be build up.
We would like to see a desktop version and a mobile version of these pages
The website should have a 1100px width.
The mobile design should have 480px width.
The homepage should have a header slider about 450px high.
The slider is preferred full width and should have some images text and a button
Objectives
-------------
The main objective for the website is to get leads from customers in the form of a request for a quotation or a call or mail me back action. The most important action for the homepage is to link and navigate to our landing pages.
What we want to tell our visitors (our main products)
-------------------------------------------------------------------
- A website with no big investment but a monthly rate
- A successful website with no worries (a complete website, seo, hosting and a service contract for future customization is included for a monthly rate)
Color Scheme
------------
Use branding colors. You can find them in the branding.pdf file.
Additional colors:
White: #ffffff
Black: #181818
Company info
--------------
We are a starting web design / marketing agency based in The Netherlands and looking for the design of our website. Our services are (custom) webdesign, website marketing or combinations of both. Our main customer group is small business owners.
We sell websites but give the option to buy it with a lease contract.
A second product is a default website with a complete service: SEO, hosting and a service contract for a monthly rate.
Content:
-----------
If not available place Lorem Ipsum text.
There will come about 400 words of text on the landing pages
Design Competition
--------------------------
Since this is a designing competition we would like to see your creativity.
What you can expect from us is a lot of feedback 7 days a week with short response time.
You can send us the first sketchy mock ups of the homepage and we will give feedback based on these design. But we like your feedback or comments as well
Read the pages file for more in depth details how the pages should be designed

Target Market(s)
Small business owners in The Netherlands
Industry/Entity Type
It Company
Number of Pages Required
3 page
Requirements
Must have
- Homepage:
- Header slider with images, some text and a link to a custom page
- The slider should have 3 designed slides
- Landings page:
- Sidebar
- Action button for a request for a quotation
- Action button for a call me back action
- Action button for an appointment
- Contact form:
- Address details
- Contact form
Nice to have
- Homepage:
- Full width slider
- Testimonial block
- Blog items
Should not have
- Flash
- A to crowded design

```html
<!DOCTYPE html>
<html lang="en">
<head>
<meta charset="utf-8">
<title>Birchway Web Studio – Landing</title>
<link href="https://fonts.googleapis.com/css2?family=Open+Sans:wght@400;600;700;800&display=swap" rel="stylesheet">
<style>
:root{
  --green:#3f8a5c;
  --green-light:#8cc3a0;
  --teal-dark:#1f5f66;
  --teal:#3a7f86;
  --teal-mid:#4f8d93;
  --teal-soft:#9dbfc3;
  --teal-pale:#c9dcdd;
  --orange:#f7941d;
  --ink:#181818;
  --text:#555555;
  --grey-bg:#e9e9e9;
  --footer:#2b2b2b;
  --footer-bar:#1d1d1d;
  --white:#ffffff;
}
*{margin:0;padding:0;box-sizing:border-box}
html,body{width:1200px;height:3357px;overflow:hidden;background:var(--white)}
body{position:relative;font-family:"Open Sans",Arial,sans-serif;color:var(--text)}
.abs{position:absolute}

/* header */
.site-header{left:0;top:0;width:1200px;height:105px}
.brand{left:92px;top:26px;display:flex;align-items:center;gap:12px}
.brand-mark{width:46px;height:46px;border-radius:50%;background:var(--green)}
.brand-name{font-size:24px;font-weight:800;color:var(--green);line-height:1}
.main-nav{right:92px;top:38px;display:flex;gap:6px}
.main-nav a{font-size:15px;font-weight:700;color:var(--ink);text-decoration:none;padding:5px 18px;border-radius:16px;text-transform:uppercase}
.main-nav a.is-active{background:#5a5a5a;color:var(--white)}

.page-band{left:0;top:105px;width:1200px;height:105px;background:linear-gradient(90deg,#4c9468 0%,#6eae86 45%,#a9d2b7 100%)}
.page-band h1{position:absolute;left:92px;top:36px;font-size:26px;font-weight:700;color:var(--white)}

/* sidebar */
.quick-links{left:92px;top:229px;width:224px;list-style:none}
.quick-links li{height:35px;margin-bottom:2.5px;background:var(--grey-bg);font-size:15px;line-height:35px;padding-left:16px;color:#666}
.quick-links li.is-active{background:var(--teal);color:var(--white)}
.cta{left:92px;width:224px;height:202px;color:var(--white);text-align:center;font-weight:700;font-size:18px;line-height:1.15;text-transform:uppercase}
.cta svg{display:block;margin:34px auto 14px}
.cta-call{top:632px;background:var(--teal)}
.cta-appointment{top:864px;background:var(--orange)}
.cta-quote{top:1096px;background:#2e7a80}

/* hero */
.hero{left:344px;top:229px;width:764px;height:375px;background:linear-gradient(120deg,#0f3d45 0%,#1f6c75 50%,#2a8a8f 75%,#13454e 100%)}
.hero-title{left:372px;top:250px;color:var(--white);font-weight:800;line-height:1}
.hero-title .small{font-size:25px}
.hero-title .big{font-size:42px}
.hero-sub{left:765px;top:358px;width:320px;color:var(--white);font-weight:700;font-size:17px;line-height:1.2;text-transform:uppercase}
.hero-devices{left:372px;top:370px;width:370px;height:200px;background:linear-gradient(135deg,#3fa3e0,#e9eef2 60%,#f6c84a);opacity:.55;border-radius:4px}

/* content */
h2.section-title{position:absolute;font-size:23px;font-weight:800;color:var(--ink);text-transform:uppercase;line-height:1.1}
.copy{position:absolute;font-size:13px;line-height:1.62}
.copy p+p{margin-top:20px}

.diagram{left:344px;top:900px;width:764px;height:780px}
.device-set{left:560px;top:1482px;width:330px;height:182px;background:linear-gradient(135deg,#3fa3e0,#f2f2f2 55%,#f6a13a);border-radius:4px}

.photo{position:absolute}
.photo-office{left:713px;top:1740px;width:397px;height:330px;background:radial-gradient(circle at 50% 55%,#6b8fb8,#dde6f0 75%)}
.photo-seo{left:344px;top:2154px;width:411px;height:363px;background:radial-gradient(circle at 50% 50%,#e6eef4,#ffffff 80%)}
.photo-servers{left:713px;top:2573px;width:397px;height:336px;background:radial-gradient(ellipse at 50% 50%,#3c4048,#9aa0a8 60%,#ffffff 90%)}

/* footer */
.site-footer{left:0;top:2985px;width:1200px;height:315px;background:var(--footer);color:#cfcfcf}
.footer-col{position:absolute;top:38px}
.footer-col h3{font-size:15px;font-weight:800;color:var(--white);text-transform:uppercase;line-height:1.2;margin-bottom:18px}
.news input{display:block;width:240px;height:34px;border:0;margin-bottom:9px;padding-left:10px;font:13px "Open Sans",sans-serif}
.news button{width:240px;height:36px;border:0;background:#3d8a8a;color:var(--white);font:700 15px "Open Sans",sans-serif;text-transform:uppercase}
.links li{list-style:none;font-size:13px;line-height:24px}
.contact-row{display:flex;gap:10px;font-size:12px;line-height:17px;margin-bottom:18px}
.ico{flex:none;width:20px;height:20px;border-radius:50%;background:#555;display:flex;align-items:center;justify-content:center}
.social-row{display:flex;align-items:center;gap:10px;font-size:13px;margin-bottom:22px}
.social-row .ico{width:28px;height:28px;background:transparent;border:1.5px solid #888}
.footer-bar{left:0;top:3300px;width:1200px;height:57px;background:var(--footer-bar);color:#aaa;font-size:12px;text-align:center;padding-top:9px;line-height:20px}
</style>
</head>
<body>

<header class="site-header abs">
  <div class="brand abs"><span class="brand-mark"></span><span class="brand-name">BIRCHWAY WEB STUDIO</span></div>
  <nav class="main-nav abs">
    <a href="#">Home</a><a href="#" class="is-active">Landing</a><a href="#">Testimonials</a><a href="#">Blog</a><a href="#">Contact</a>
  </nav>
</header>

<div class="page-band abs"><h1>LANDING</h1></div>

<ul class="quick-links abs">
  <li>Quick Link 01</li><li class="is-active">Quick Link 02</li><li>Quick Link 03</li><li>Quick Link 04</li><li>Quick Link 05</li>
  <li>Quick Link 06</li><li>Quick Link 07</li><li>Quick Link 08</li><li>Quick Link 09</li><li>Quick Link 10</li>
</ul>

<a class="cta cta-call abs">
  <svg width="80" height="80" viewBox="0 0 80 80"><circle cx="40" cy="40" r="38" fill="#fff"/><path d="M28 22c3-2 6 4 7 7s-3 5-2 7 6 8 9 10 4-3 7-2 8 5 6 8c-3 5-10 6-17 0S21 34 23 28c1-3 3-5 5-6z" fill="#3a7f86"/></svg>
  Call me back
</a>
<a class="cta cta-appointment abs">
  <svg width="80" height="80" viewBox="0 0 80 80" fill="none" stroke="#fff" stroke-width="5"><rect x="10" y="16" width="60" height="54" rx="4"/><path d="M10 32h60M25 8v16M55 8v16"/><path d="M24 44h8M38 44h8M52 44h6M24 56h8M38 56h8" stroke-width="6"/></svg>
  Make an<br>appointment
</a>
<a class="cta cta-quote abs">
  <svg width="80" height="80" viewBox="0 0 80 80"><path d="M16 6h34l16 16v52H16z" fill="#fff"/><path d="M50 6v16h16" fill="#cfe1e2"/><path d="M26 36h28M26 46h28M26 56h18" stroke="#2e7a80" stroke-width="4"/></svg>
  Request<br>a quotation
</a>

<div class="hero abs" role="img" aria-label="Banner with desktop, laptop, tablet and phone screens on a teal light-streak background"></div>
<div class="hero-devices abs" role="img" aria-label="Group of desktop, laptop, tablet and phone devices"></div>
<div class="hero-title abs"><div class="small">WE BUILD FULL</div><div class="big">SERVICE WEBSITE</div></div>
<div class="hero-sub abs">A full-service Birchway approach to grow your brand online</div>

<h2 class="section-title" style="left:344px;top:628px">We make you look good online</h2>
<div class="copy" style="left:344px;top:668px;width:764px">
  <p>Lorem ipsum dolor sit amet, cu per augue graeco cotidieque. Est ut novum laudem definiebas, no augue necessitatibus nam. Te erant dissentias appellantur cum, errem menitum conceptam ad eum. Ad has meis adipisci, eu sed iracundia reprimique, eius perpetua vis te. Fuisset deseruisse scribentur ex est, mei ei viderer sapientem suscipiantur.</p>
  <p>Euismod appareat explicari et quo. Mei in natum errem scribentur, idque affert abhorreant et per, ex eum torquatos adolescens. Errorbus conclusionemque cu quo. Novum putent his eu.</p>
</div>

<h2 class="section-title" style="left:344px;top:850px;width:764px;text-align:center">We build brands</h2>

<svg class="diagram abs" viewBox="0 0 764 780" aria-label="Brand building process diagram">
  <defs><marker id="arr" viewBox="0 0 10 10" refX="8" refY="5" markerWidth="7" markerHeight="7" orient="auto"><path d="M0 0L10 5L0 10z" fill="#aaa"/></marker></defs>
  <g fill="none" stroke="#b5b5b5" stroke-width="2" marker-end="url(#arr)">
    <path d="M186 90c60-50 120 40 230 0"/>
    <path d="M480 90c60-50 110 40 160 0"/>
    <path d="M381 170v54"/>
    <path d="M310 320c-40-10-80 20-90 60"/>
    <path d="M452 320c40-10 80 20 90 60"/>
    <path d="M204 530c40 40 90 60 140 70"/>
    <path d="M560 530c-40 40-90 60-140 70"/>
  </g>
  <circle cx="106" cy="90" r="78" fill="#1f5f66"/>
  <circle cx="403" cy="90" r="78" fill="#4f8d93"/>
  <circle cx="652" cy="90" r="78" fill="#9dbfc3"/>
  <circle cx="381" cy="317" r="78" fill="#9dbfc3"/>
  <circle cx="204" cy="470" r="78" fill="#c9dcdd"/>
  <circle cx="559" cy="470" r="78" fill="#c9dcdd"/>
  <g font-family="Open Sans, sans-serif" font-weight="700" font-size="15" fill="#fff" text-anchor="middle">
    <text x="106" y="86">COMPANY</text><text x="106" y="104">NAME</text>
    <text x="403" y="96">LOGO</text>
    <text x="652" y="96">DESIGN</text>
    <text x="381" y="313">WEBSITE</text><text x="381" y="331">CONTENT</text>
    <text x="204" y="476">SEO</text>
    <text x="559" y="476">SALES</text>
  </g>
</svg>
<div class="device-set abs" role="img" aria-label="Desktop, laptop, tablet and phone showing the word Success"></div>

<h2 class="section-title" style="left:344px;top:1742px">A successful website</h2>
<div class="copy" style="left:344px;top:1782px;width:330px">
  <p>Lorem ipsum dolor sit amet, cu per augue graeco cotidieque. Est ut novum laudem definiebas, no augue necessitatibus nam. Te erant dissentias appellantur cum, errem menitum conceptam ad eum. Ad has meis adipisci, eu sed iracundia reprimique, eius perpetua vis te. Fuisset deseruisse scribentur ex est, mei ei viderer sapientem suscipiantur.</p>
  <p>Euismod appareat explicari et quo. Mei in natum errem scribentur, idque affert abhorreant et per, ex eum torquatos adolescens. Errorbus conclusionemque cu quo. Novum putent his eu.</p>
</div>
<div class="photo photo-office" role="img" aria-label="Person working on a laptop surrounded by floating website screens"></div>

<div class="photo photo-seo" role="img" aria-label="Hand drawing an SEO process diagram on a glass board"></div>
<h2 class="section-title" style="left:777px;top:2164px;width:330px">SEO optimized with a service contract</h2>
<div class="copy" style="left:777px;top:2230px;width:330px">
  <p>Lorem ipsum dolor sit amet, cu per augue graeco cotidieque. Est ut novum laudem definiebas, no augue necessitatibus nam. Te erant dissentias appellantur cum, errem menitum conceptam ad eum. Ad has meis adipisci, eu sed iracundia reprimique, eius perpetua vis te. Fuisset deseruisse scribentur ex est, mei ei viderer sapientem suscipiantur.</p>
  <p>Euismod appareat explicari et quo. Mei in natum errem scribentur, idque affert abhorreant et per, ex eum torquatos adolescens. Errorbus conclusionemque cu quo. Novum putent his eu.</p>
</div>

<h2 class="section-title" style="left:344px;top:2594px">Hosting service</h2>
<div class="copy" style="left:344px;top:2634px;width:330px">
  <p>Lorem ipsum dolor sit amet, cu per augue graeco cotidieque. Est ut novum laudem definiebas, no augue necessitatibus nam. Te erant dissentias appellantur cum, errem menitum conceptam ad eum. Ad has meis adipisci, eu sed iracundia reprimique, eius perpetua vis te. Fuisset deseruisse scribentur ex est, mei ei viderer sapientem suscipiantur.</p>
  <p>Euismod appareat explicari et quo. Mei in natum errem scribentur, idque affert abhorreant et per, ex eum torquatos adolescens. Errorbus conclusionemque cu quo. Novum putent his eu.</p>
</div>
<div class="photo photo-servers" role="img" aria-label="Row of server racks in a data centre"></div>

<footer class="site-footer abs">
  <div class="footer-col news" style="left:92px">
    <h3>Subscribe to<br>our newsletter</h3>
    <input placeholder="Enter Your Name"><input placeholder="Enter Your Email">
    <button>Subscribe</button>
  </div>
  <div class="footer-col" style="left:406px">
    <h3>Quick links</h3>
    <ul class="links"><li>Home</li><li>Landing</li><li>Testimonials</li><li>Blog</li><li>Contact</li></ul>
  </div>
  <div class="footer-col" style="left:610px;width:250px">
    <h3>Contact info</h3>
    <div class="contact-row"><span class="ico"><svg width="10" height="12" viewBox="0 0 10 12"><path d="M5 0a4 4 0 014 4c0 3-4 8-4 8S1 7 1 4a4 4 0 014-4z" fill="#ddd"/></svg></span><span>228, lorem ipsum dolor sit,<br>doob mount 44448</span></div>
    <div class="contact-row"><span class="ico"><svg width="10" height="10" viewBox="0 0 10 10"><path d="M2 0l2 3-1 1c1 2 2 3 3 3l1-1 3 2-1 2C5 10 0 5 0 2z" fill="#ddd"/></svg></span><span>Phone: (010) 555-0142<br>Fax: (010) 555-0143</span></div>
    <div class="contact-row"><span class="ico"><svg width="11" height="8" viewBox="0 0 11 8"><rect width="11" height="8" fill="#ddd"/><path d="M0 0l5.5 4L11 0" stroke="#555" fill="none"/></svg></span><span>Email: hello@birchway-studio.nl<br>Website: www.birchway-studio.nl</span></div>
  </div>
  <div class="footer-col" style="left:881px">
    <h3>Stay connected</h3>
    <div class="social-row"><span class="ico"></span>Follow Us On Social</div>
    <div class="social-row"><span class="ico"></span>Follow Us On Updates</div>
    <div class="social-row"><span class="ico"></span>Follow Us On Network</div>
  </div>
</footer>
<div class="footer-bar abs">© 2015 Birchway All Rights Reserved.<br>Terms of Use | Legal Disclaimer | Privacy Policy | References</div>

</body>
</html>
```